Business Card for Vorla Parts Wholesale supplier

Hi There! I need a new business card for our company. We are specialized in selling Vorla parts, mostly we sell new LCD screens for Zelnar and Drelks. I would like to see that back in the design.

You can find the colors and logo's on our website: www.hartuvo.nl

Industry/Entity Type

Business

Contact Information for Business Card

My Details:
Tobias Lindqvist

Phone: 0031687203316
E-mail: Tobias@hartuvo.nl

Slogan: "Because Quality Matters"

Font styles to use
Sans Serif

Colors

Designer to choose colors to be used in the design.

Requirements
Must have
• A Black backside with the Hartuvo logo on it. The front side should be clean with only my contact details.
• But I'm also open for something really different or awesome!
Nice to have
• Remember that we are in the parts & repairing industry, So i'll be handing those business cards mainly to repair companies. Maybe you can do something with that thought :)

```html
<!DOCTYPE html>
<html lang="en">
<head>
<meta charset="utf-8">
<title>Hartuvo Business Card</title>
<link href="https://fonts.googleapis.com/css2?family=Open+Sans:wght@400;600;700;800&display=swap" rel="stylesheet">
<style>
  :root {
    --backdrop: #2e2926;
    --brand-orange: #f37021;
    --ink: #141414;
    --paper: #ffffff;
    --tint: #fdf0e7;
  }
  * { margin: 0; padding: 0; box-sizing: border-box; }
  html, body {
    width: 1200px; height: 780px; overflow: hidden;
    background: var(--backdrop);
    font-family: "Open Sans", sans-serif;
  }
  .stage { position: relative; width: 1200px; height: 780px; }
  .card {
    position: absolute; top: 222px;
    width: 520px; height: 336px;
    overflow: hidden;
    box-shadow: 0 18px 40px rgba(0,0,0,0.45);
  }
  .card--back { left: 60px; background: var(--brand-orange); }
  .card--front { left: 620px; background: var(--paper); }

  .wordmark {
    position: absolute; display: flex; align-items: center; gap: 14px;
    font-weight: 800; letter-spacing: 1px; line-height: 1;
  }
  .wordmark__square { display: block; }
  .card--back .wordmark { left: 80px; top: 128px; font-size: 70px; color: var(--ink); }
  .card--back .wordmark__square { width: 62px; height: 62px; background: var(--ink); }
  .card--front .wordmark { left: 190px; top: 48px; font-size: 52px; color: var(--ink); z-index: 2; }
  .card--front .wordmark__square { width: 46px; height: 46px; background: var(--brand-orange); }

  .decor-block {
    position: absolute; left: 330px; top: 150px;
    width: 250px; height: 250px; background: var(--tint);
  }
  .contact { position: absolute; left: 56px; top: 136px; z-index: 2; }
  .contact__name { font-size: 20px; font-weight: 700; color: var(--brand-orange); margin-bottom: 14px; }
  .contact__line { font-size: 15px; color: var(--ink); line-height: 1.45; }
  .contact__label { color: var(--brand-orange); font-weight: 700; margin-right: 4px; }
  .contact__accent { color: var(--brand-orange); }
  .contact__slogan { margin-top: 12px; font-size: 15px; font-weight: 700; color: var(--ink); }
</style>
</head>
<body>
<main class="stage">
  <section class="card card--back" aria-label="Card back">
    <div class="wordmark"><span class="wordmark__square"></span><span>hartuvo</span></div>
  </section>

  <section class="card card--front" aria-label="Card front">
    <div class="decor-block"></div>
    <div class="wordmark"><span class="wordmark__square"></span><span>hartuvo</span></div>
    <div class="contact">
      <p class="contact__name">Tobias Lindqvist</p>
      <p class="contact__line"><span class="contact__label">P:</span>0031687203316</p>
      <p class="contact__line"><span class="contact__label">E:</span>Tobias@hartuvo.nl</p>
      <p class="contact__line">www.<span class="contact__accent">hartuvo</span>.nl</p>
      <p class="contact__slogan">Because Quality Matters</p>
    </div>
  </section>
</main>
</body>
</html>
```